A comprehensive online math curriculum teaching service needs a Landing Page design

We need a Landing Page design for a startup company based in Edmonton, Alberta, Canada, called Brevanta Numérica. Brevanta Numérica is a comprehensive online math curriculum service for independently schooled students in grades 6-12 worldwide. Instruction is delivered through a one-on-one, virtual, adaptive classroom that uses integrated, interactive digital whiteboards for both teachers and students, with a standard modular lesson workflow for mastering math. Brevanta Numérica is designed to help students from all socioeconomic backgrounds master mathematics.

The landing Page should use the same colour scheme as our recently designed PowerPoint template (attached for reference: Design 36712224). Our logo is in the PowerPoint template. I also attached a draft wireframe of our landing page to guide the design.

Target Market(s)

Independently schooled students in grades 6 through 12 worldwide

Industry/Entity Type

Education - Mathematics teaching

Requirements
Must have
• Consistent colours with PowerPoint design

```html
<!DOCTYPE html>
<html lang="en">
<head>
<meta charset="utf-8">
<title>Brevanta Numérica — Online Math Academy</title>
<link href="https://fonts.googleapis.com/css2?family=Montserrat:wght@400;500;600;700;800&display=swap" rel="stylesheet">
<style>
:root{
  --blue:#2f6bef;
  --blue-deep:#1e4fd0;
  --navy:#141a2b;
  --ink:#1b1f2a;
  --slate:#252c3d;
  --muted:#555c6b;
  --line:#d5dbe6;
  --footer:#e3ebfa;
  --white:#ffffff;
}
*{box-sizing:border-box;margin:0;padding:0}
html,body{width:1200px;height:4283px;overflow:hidden}
body{font-family:'Montserrat',sans-serif;color:var(--ink);background:var(--white)}
.page{position:relative;width:1200px;height:4283px}
.abs{position:absolute}

/* header */
.site-header{position:absolute;top:0;left:0;width:1200px;height:120px;background:var(--white)}
.topbar{position:absolute;top:0;left:602px;width:598px;height:33px;display:flex}
.topbar a{display:flex;align-items:center;justify-content:center;color:#fff;text-decoration:none;font-size:15px;font-weight:600}
.topbar .register{width:268px;background:var(--navy);clip-path:polygon(5% 0,100% 0,100% 100%,0 100%)}
.topbar .consult{flex:1;background:var(--blue);margin-left:-14px;clip-path:polygon(5% 0,100% 0,100% 100%,0 100%)}
.brand{position:absolute;left:118px;top:22px;display:flex;align-items:flex-start;gap:18px}
.brand-dot{width:36px;height:36px;border-radius:50%;background:var(--blue);margin-top:12px}
.brand-name{font-size:35px;font-weight:500;color:var(--ink);line-height:1.1;border-left:2px solid var(--ink);padding-left:16px}
.brand-tag{font-size:17px;font-weight:500;color:var(--ink);margin-top:10px;padding-left:18px}
.main-nav{position:absolute;left:595px;top:72px;display:flex;font-size:12px;font-weight:500;color:var(--ink)}
.main-nav span{padding:0 14px;border-right:1px solid var(--ink);line-height:13px}
.main-nav span:first-child{padding-left:0}
.main-nav span:last-child{border-right:none}

/* hero */
.hero{position:absolute;top:120px;left:0;width:1200px;height:680px;
  background:linear-gradient(110deg,#1b2a5e 0%,#233a86 45%,#1a3278 70%,#12204f 100%)}
.hero-copy{position:absolute;left:120px;top:38px;width:482px;color:#fff;font-size:12.3px;font-weight:600;line-height:21.5px}
.hero-copy p{margin-bottom:21px}
.hero-copy p.tight{margin-bottom:0}
.hero-buttons{position:absolute;left:120px;top:583px;display:flex;gap:18px}
.btn{display:flex;align-items:center;justify-content:center;height:41px;font-size:15px;font-weight:600;color:#fff;text-decoration:none}
.btn-solid{background:var(--blue);width:214px}
.btn-outline{border:2px solid #fff;width:214px}
.hero-art{position:absolute;left:640px;top:55px;width:520px;height:560px;border-radius:6px;
  background:linear-gradient(160deg,rgba(60,100,220,.35),rgba(20,40,110,.25))}

/* section headings */
.section-title{position:absolute;left:0;width:1200px;text-align:center;font-size:35px;font-weight:700;color:var(--ink)}
.title-bar{position:absolute;left:572px;width:56px;height:4px;background:var(--blue)}

/* stats */
.stats{position:absolute;top:968px;left:118px;width:964px;display:flex;justify-content:space-between}
.stat{width:300px;text-align:center}
.stat-num{font-size:31px;font-weight:700;color:var(--blue)}
.stat-bar{width:56px;height:3px;background:var(--blue);margin:8px auto 20px}
.stat-label{font-size:15.5px;font-weight:600;line-height:24px}

.lead{position:absolute;top:1236px;left:0;width:1200px;text-align:center;font-size:17px;font-weight:700}
.sublead{position:absolute;top:1274px;left:0;width:1200px;text-align:center;font-size:13px;color:var(--muted)}

/* challenge cards */
.card{position:absolute;width:302px;height:230px;border:2px solid var(--ink);border-radius:4px;padding:24px 22px}
.card-head{display:flex;align-items:center;gap:20px;height:80px}
.card-icon{width:64px;height:64px;border-radius:50%;background:var(--blue);flex:none}
.card-title{font-size:17.5px;font-weight:700;line-height:26px}
.card-text{font-size:13px;line-height:24px;color:var(--ink);margin-top:22px}

/* how it works */
.how{position:absolute;top:1913px;left:0;width:1200px;height:720px;
  background:radial-gradient(ellipse at 50% 40%,#3a4256 0%,#2a3144 45%,#1d2333 100%)}
.how-title{position:absolute;top:70px;left:0;width:1200px;text-align:center;color:#fff;font-size:35px;font-weight:700}
.how-sub{position:absolute;top:170px;left:0;width:1200px;text-align:center;color:#fff;font-size:17.5px;font-weight:700;line-height:28px}
.tab{position:absolute;height:42px;display:flex;align-items:center;justify-content:center;font-size:18px;font-weight:700;border-radius:3px}
.how .tab-on{background:var(--blue);color:#fff;left:241px;top:256px;width:351px}
.how .tab-off{border:2px solid #fff;color:#fff;left:610px;top:256px;width:349px}
.how-panel{position:absolute;left:138px;top:332px;width:921px;height:291px;border:2px solid var(--blue);border-radius:10px;background:rgba(22,28,44,.55);display:flex;padding:22px 16px}
.feature{flex:1;padding:0 0 0 0;color:#fff;position:relative}
.feature+.feature{border-left:1px solid #7c8498;margin:20px 0 8px;padding-left:26px}
.feature-head{display:flex;align-items:center;gap:34px;margin-left:0}
.feature+.feature .feature-head{margin-top:-20px}
.feature-icon{width:70px;height:70px;border-radius:50%;background:var(--blue);flex:none}
.feature-title{font-size:18px;font-weight:700}
.feature-text{font-size:13px;line-height:24px;margin:20px 0 0 9px;width:410px}
.learn-more{position:absolute;right:14px;bottom:6px;font-size:14px;font-weight:600;display:flex;align-items:center;gap:8px}

/* lesson design */
.lesson{position:absolute;top:2633px;left:0;width:1200px;height:1253px}
.lesson .tab{top:176px;height:75px;width:351px;font-size:18px;line-height:28px;text-align:center;border-radius:4px}
.lesson .tab-on{left:231px;background:var(--blue);color:#fff}
.lesson .tab-off{left:615px;border:2px solid var(--ink);color:var(--ink)}
.flow-line{position:absolute;left:0;top:0}
.step{position:absolute;left:0;width:1200px;height:54px}
.step-box{position:absolute;left:150px;top:0;width:239px;height:54px;display:flex;align-items:center;justify-content:center;font-size:17.5px;font-weight:700;border-radius:3px}
.step-box.dark{background:var(--ink);color:#fff}
.step-box.light{background:#fff;border:2px solid var(--blue);color:var(--ink)}
.step-num{position:absolute;left:123px;top:-23px;width:46px;height:46px;border-radius:50%;background:var(--blue);border:3px solid #fff;color:#fff;font-size:20px;font-weight:700;display:flex;align-items:center;justify-content:center}
.step-desc{position:absolute;left:447px;top:50%;transform:translateY(-50%);width:360px;font-size:13px;line-height:24px;color:var(--muted)}
.step-time{position:absolute;left:954px;top:50%;transform:translateY(-50%);font-size:17.5px;font-weight:700;line-height:27px}
.step-time small{display:block;font-size:13px;font-weight:500;color:var(--muted);line-height:18px}
.cta{position:absolute;left:492px;top:1155px;width:214px;height:40px;background:var(--blue);color:#fff;font-size:15px;font-weight:600;display:flex;align-items:center;justify-content:center}

/* footer */
.site-footer{position:absolute;top:3886px;left:0;width:1200px;height:397px;background:var(--footer)}
.footer-brand{position:absolute;left:120px;top:82px;display:flex;align-items:center;gap:16px}
.footer-brand .brand-dot{width:30px;height:30px;margin:0}
.footer-brand .brand-name{font-size:31px;border:none;padding:0}
.footer-tag{position:absolute;left:196px;top:136px;font-size:14.5px;font-weight:500}
.footer-col{position:absolute;top:70px}
.footer-col h4{font-size:17px;font-weight:600;margin-bottom:24px}
.footer-col li{list-style:none;font-size:14.5px;display:flex;align-items:center;gap:12px;height:32px}
.contact-row{display:flex;align-items:center;gap:16px;font-size:14.5px;height:48px}
.contact-icon{width:30px;height:30px;border-radius:50%;background:var(--blue);display:flex;align-items:center;justify-content:center}
.footer-rule{position:absolute;left:126px;top:316px;width:955px;height:1px;background:var(--ink)}
.copyright{position:absolute;top:338px;left:0;width:1200px;text-align:center;font-size:13.5px}
</style>
</head>
<body>
<div class="page">

  <header class="site-header">
    <div class="topbar">
      <a class="register" href="#">Register a Student</a>
      <a class="consult" href="#">Free Consultation</a>
    </div>
    <div class="brand">
      <div class="brand-dot"></div>
      <div>
        <div class="brand-name">Brevanta Numérica</div>
        <div class="brand-tag">Inspiring Math • Empowering Learning</div>
      </div>
    </div>
    <nav class="main-nav">
      <span>FEATURES</span><span>PROGRAM</span><span>TUITION</span><span>ABOUT US</span><span>CONTACT US</span>
    </nav>
  </header>

  <section class="hero" role="img" aria-label="Background photo of students learning math online, tinted deep blue">
    <div class="hero-copy">
      <p>Brevanta Numérica – accelerated educational outcome is a comprehensive online math curriculum teaching service for independently schooled students in grades 6 through 12 worldwide. Teaching is done through our math academy, a one-on-one, virtual adaptive classroom that uses integrated, interactive digital whiteboards for both teachers and students. Brevanta Math Academy will open its virtual doors for the first cohort of grade 6 students in September 2026.</p>
      <p>Registration for Term One math classes opens on June 1, 2026 and closes in the middle of August 2026.</p>
      <p>Brevanta Numérica is designed to help students from all socioeconomic backgrounds master mathematics. We teach comprehensive grade 6-12 math curricula to independently schooled students.</p>
      <p class="tight">Online, interactive math sessions are delivered in secure virtual classrooms with integrated digital whiteboards for both teacher and student. Real-time one-on-one synchronous math sessions led by qualified experts.</p>
      <p>We teach modular math lessons that use an incremental development methodology, grounded in continuous practice and review. Our math lessons are designed in small 1 ½-hour units, each covering a new math concept that can be taught in 20 minutes, allowing students ample time to practice the newly introduced math skills daily.</p>
    </div>
    <div class="hero-buttons">
      <a class="btn btn-solid" href="#">Register a Student</a>
      <a class="btn btn-outline" href="#">Free Consultation</a>
    </div>
    <div class="hero-art" role="img" aria-label="Line illustration of a teacher at a whiteboard connected to three students at desks, titled Brevanta Math Academy"></div>
  </section>

  <h2 class="section-title" style="top:880px">Program Overview</h2>
  <div class="title-bar" style="top:936px"></div>
  <div class="stats">
    <div class="stat"><div class="stat-num">90+</div><div class="stat-bar"></div><div class="stat-label">Structured Lessons per Grade</div></div>
    <div class="stat"><div class="stat-num">20+</div><div class="stat-bar"></div><div class="stat-label">Homework Questions and<br>Solutions per Lesson</div></div>
    <div class="stat"><div class="stat-num">20+</div><div class="stat-bar"></div><div class="stat-label">Assessment tests per Grade<br>Program</div></div>
  </div>

  <h2 class="section-title" style="top:1150px">Proficiency</h2>
  <div class="title-bar" style="top:1206px"></div>
  <p class="lead">Making math education engaging, effective, and within everyone’s reach.</p>
  <p class="sublead">Teaching math to independently schooled students is not easy. We know the challenges:</p>

  <article class="card" style="left:118px;top:1323px">
    <div class="card-head"><div class="card-icon"></div><h3 class="card-title">Limited subject<br>expertise</h3></div>
    <p class="card-text">Struggling with advanced topics, forgotten knowledge, and specialized methods.</p>
  </article>
  <article class="card" style="left:449px;top:1323px">
    <div class="card-head"><div class="card-icon"></div><h3 class="card-title">Ensuring<br>conceptual<br>understanding</h3></div>
    <p class="card-text">Over-reliance on procedures. Bridging the “why” of math and real-world applications.</p>
  </article>
  <article class="card" style="left:779px;top:1323px">
    <div class="card-head"><div class="card-icon"></div><h3 class="card-title">Curriculum<br>challenges</h3></div>
    <p class="card-text">How can I choose the right curriculum and supplementary materials? Can I successfully adapt pre-made plans?</p>
  </article>
  <article class="card" style="left:118px;top:1580px">
    <div class="card-head"><div class="card-icon"></div><h3 class="card-title">Preparing for<br>advanced math</h3></div>
    <p class="card-text" style="margin-top:8px">Am I preparing my child for advanced math and for successfully transitioning into higher education, skilled jobs, or entrepreneurship?</p>
  </article>
  <article class="card" style="left:449px;top:1580px">
    <div class="card-head"><div class="card-icon"></div><h3 class="card-title">Assessment and<br>feedback</h3></div>
    <p class="card-text" style="margin-top:4px">Am I using the proper evaluation process to assess my child’s progress and identify their weaknesses?<br>Am I providing timely feedback to my child?</p>
  </article>
  <article class="card" style="left:779px;top:1580px">
    <div class="card-head"><div class="card-icon"></div><h3 class="card-title">Keeping math<br>fun and engaging</h3></div>
    <p class="card-text">Creativity struggles, gamification challenges and overcoming math fatigue.</p>
  </article>

  <section class="how" role="img" aria-label="Dimmed background photo of a student working at a laptop">
    <h2 class="how-title">How Brevanta Numérica Works</h2>
    <p class="how-sub">Teaching comprehensive math curricula to independently schooled students<br>in grades 6-12 through secure virtual classrooms.</p>
    <div class="tab tab-on">Pedagogical Methodology</div>
    <div class="tab tab-off">Virtual Classroom</div>
    <div class="how-panel">
      <div class="feature">
        <div class="feature-head"><div class="feature-icon"></div><h3 class="feature-title">Effective Curriculum</h3></div>
        <p class="feature-text">Time-tested and proven pedagogical methodology with three pillars:<br>(1) new math concepts built on previously taught ones;<br>(2) daily review of earlier math concepts to increase understanding; and<br>(3) frequent, cumulative assessments to ensure students master each math skill as new ones are added.</p>
      </div>
      <div class="feature">
        <div class="feature-head"><div class="feature-icon"></div><h3 class="feature-title">Innovative Lesson Design</h3></div>
        <p class="feature-text">Standard, modular 1 ½ hour lesson workflows designed to accelerate students’ mastery of math skills and concepts.</p>
        <div class="learn-more">Learn More
          <svg width="18" height="12" viewBox="0 0 18 12"><path d="M1 6h15M11 1l5 5-5 5" fill="none" stroke="#fff" stroke-width="1.8"/></svg>
        </div>
      </div>
    </div>
  </section>

  <section class="lesson">
    <h2 class="section-title" style="top:98px">Innovative Lesson Design</h2>
    <div class="title-bar" style="top:154px"></div>
    <div class="tab tab-on">1 and ½ Hour Session Lesson<br>Workflow Grades 6 to 8</div>
    <div class="tab tab-off">1 and 1/2 Hour Session Lesson<br>Workflow Grades 9 to 12</div>

    <svg class="flow-line" width="1200" height="1150" viewBox="0 0 1200 1150" aria-hidden="true">
      <g stroke="#2f6bef" stroke-width="2" fill="none">
        <path d="M268 389V1130" stroke-dasharray="6 5"/>
        <path d="M261 444l7 8 7-8M261 556l7 8 7-8M261 662l7 8 7-8M261 772l7 8 7-8M261 893l7 8 7-8M261 1021l7 8 7-8M261 1128l7 8 7-8"/>
      </g>
    </svg>

    <div class="step" style="top:335px">
      <div class="step-box dark">Preparation</div><div class="step-num">1</div>
      <p class="step-desc">Promotes mental math and problem-solving and setting the tone for the day’s teaching</p>
      <div class="step-time">15 Minutes</div>
    </div>
    <div class="step" style="top:463px">
      <div class="step-box light">Facts practices</div>
      <p class="step-desc">Students practice to recall immediately or quickly calculate simple math facts. Timed event to promote the fast recall of basic facts.</p>
      <div class="step-time">6 &nbsp;Minutes<small>Timed Event</small></div>
    </div>
    <div class="step" style="top:570px">
      <div class="step-box light">Mental math</div>
      <p class="step-desc">Students listen to problem and perform calculation mentally and write the answer. Timed event to promote agility.</p>
      <div class="step-time">4 &nbsp;Minutes<small>Timed Event</small></div>
    </div>
    <div class="step" style="top:676px">
      <div class="step-box light">Problem Solving</div>
      <p class="step-desc">Students practice critical-thinking skills daily.</p>
      <div class="step-time">5 &nbsp;Minutes<small>Timed Event</small></div>
    </div>
    <div class="step" style="top:786px">
      <div class="step-box dark">New concept</div><div class="step-num">2</div>
      <p class="step-desc">Introduces new math concepts in small increments.</p>
      <div class="step-time">20 Minutes</div>
    </div>
    <div class="step" style="top:907px">
      <div class="step-box dark">Lesson practice</div><div class="step-num">3</div>
      <p class="step-desc">Opportunity for students to practice skills of new math concepts.</p>
      <div class="step-time">40 minutes</div>
    </div>
    <div class="step" style="top:1035px">
      <div class="step-box dark">Homework</div><div class="step-num">4</div>
      <p class="step-desc">Twenty-five to thirty problems to provide students with distributed practice that promote long-term retention of math concepts.</p>
      <div class="step-time">1 hour and 30<br>minutes<br>per session</div>
    </div>

    <a class="cta" href="#">Free Consultation</a>
  </section>

  <footer class="site-footer">
    <div class="footer-brand"><div class="brand-dot"></div><div class="brand-name">Brevanta Numérica</div></div>
    <div class="footer-tag">Inspiring Math • Empowering Learning</div>
    <div class="footer-col" style="left:565px">
      <h4>QUICK LINKS</h4>
      <ul>
        <li><svg width="12" height="12" viewBox="0 0 12 12"><path d="M0 6h10M6 2l4 4-4 4" fill="none" stroke="#1b1f2a" stroke-width="2"/></svg>Home</li>
        <li><svg width="12" height="12" viewBox="0 0 12 12"><path d="M0 6h10M6 2l4 4-4 4" fill="none" stroke="#1b1f2a" stroke-width="2"/></svg>Features</li>
        <li><svg width="12" height="12" viewBox="0 0 12 12"><path d="M0 6h10M6 2l4 4-4 4" fill="none" stroke="#1b1f2a" stroke-width="2"/></svg>Program</li>
        <li><svg width="12" height="12" viewBox="0 0 12 12"><path d="M0 6h10M6 2l4 4-4 4" fill="none" stroke="#1b1f2a" stroke-width="2"/></svg>Tuition</li>
        <li><svg width="12" height="12" viewBox="0 0 12 12"><path d="M0 6h10M6 2l4 4-4 4" fill="none" stroke="#1b1f2a" stroke-width="2"/></svg>About Us</li>
        <li><svg width="12" height="12" viewBox="0 0 12 12"><path d="M0 6h10M6 2l4 4-4 4" fill="none" stroke="#1b1f2a" stroke-width="2"/></svg>Contact Us</li>
      </ul>
    </div>
    <div class="footer-col" style="left:800px">
      <h4>CONTACT US</h4>
      <div class="contact-row"><span class="contact-icon"><svg width="14" height="14" viewBox="0 0 24 24"><path d="M6.6 10.8a15 15 0 006.6 6.6l2.2-2.2a1 1 0 011-.25 11.4 11.4 0 003.6.57 1 1 0 011 1V20a1 1 0 01-1 1A17 17 0 013 4a1 1 0 011-1h3.5a1 1 0 011 1c0 1.25.2 2.45.57 3.57a1 1 0 01-.25 1z" fill="#fff"/></svg></span>+1 780-555-0148</div>
      <div class="contact-row"><span class="contact-icon"><svg width="14" height="12" viewBox="0 0 14 12"><rect x="1" y="1" width="12" height="10" rx="1" fill="none" stroke="#fff" stroke-width="1.5"/><path d="M1 2l6 5 6-5" fill="none" stroke="#fff" stroke-width="1.5"/></svg></span>hello@brevantanumerica.example</div>
    </div>
    <div class="footer-rule"></div>
    <p class="copyright">© 2026 Brevanta Numérica I All Rights Reserved</p>
  </footer>

</div>
</body>
</html>
```